Business card for Eyelash extension salon in Beverly Hills,California USA

We need new business card for our salon in Beverly Hills. The salon name is 'Lashvera' . We would like to have...Business name: Lashvera Name of person: will provide later Address 4720 N.Alder Crest Ave Beverly Hills , CA 90210 Phone: will provide later (Text only) Web: www.lashverastudio.example Snapgrid icon, Circlebook icon follow us for seasonal campaign and news @lashverastudiolounge Design should look elegant, high-end, clean, simple, cohesive with my brand. Please refer my brand board. Business name color will be metallic bronzy color. Im thinking grey background or white background. Thanks

Target Market(s)

25-35. Gender neutral. People who are in Entertainment business industry.
This is High-end Eyelash extension salon in Beverly Hills

Industry/Entity Type

Beauty Salon

Contact Information for Business Card

Business name: Lashvera
Name of person: will provide later
Address 4720 N.Alder Crest Ave Beverly Hills , CA 90210
Phone: will provide later (Text only)
Web: www.lashverastudio.example
Snapgrid icon, Circlebook icon
follow us for seasonal campaign and news @lashverastudiolounge

Requirements
Must have
• Beautiful, elegant, clean and simple look but very attractive and modern
Should not have
• We don't like too clutter, too busy designs.

```html
<!DOCTYPE html>
<html lang="en">
<head>
<meta charset="utf-8">
<title>Lashvera Business Card</title>
<link rel="stylesheet" href="https://fonts.googleapis.com/css2?family=Playfair+Display:wght@400;700&family=Josefin+Sans:wght@400&display=swap">
<style>
  :root {
    --bronze: #8a674d;
    --bronze-text: #8b6a52;
    --paper: #f4f4f3;
    --ink-light: #ffffff;
    --stage: #2a2a2a;
    --marble-light: #f1f1f1;
    --marble-mid: #d9d9d9;
    --serif: "Playfair Display", Georgia, serif;
    --sans: "Josefin Sans", Arial, sans-serif;
  }
  * { margin: 0; padding: 0; box-sizing: border-box; }
  html, body { width: 1200px; height: 960px; overflow: hidden; }
  body { background: var(--stage); position: relative; font-family: var(--serif); }

  .card {
    position: absolute;
    width: 600px;
    height: 343px;
    overflow: hidden;
    box-shadow: 0 4px 12px rgba(0,0,0,0.45);
  }
  .card-front { left: 186px; top: 113px; background: var(--paper); }
  .card-back { left: 434px; top: 511px; }

  .front-shape { position: absolute; inset: 0; }

  .contact-block {
    position: absolute;
    left: 29px;
    top: 74px;
    color: var(--ink-light);
  }
  .person-name {
    font-family: var(--serif);
    font-weight: 700;
    font-size: 22px;
    letter-spacing: 0.5px;
    line-height: 1;
  }
  .person-role {
    font-weight: 700;
    font-size: 14px;
    margin-top: 4px;
    letter-spacing: 0.3px;
  }
  .address {
    font-size: 14px;
    line-height: 18px;
    margin-top: 31px;
  }
  .contact-list {
    list-style: none;
    font-size: 14px;
    line-height: 19.5px;
    margin-top: 11px;
  }
  .contact-list li { display: flex; align-items: center; gap: 8px; }
  .contact-list svg { width: 13px; height: 13px; flex: none; fill: var(--ink-light); }

  .brand {
    position: absolute;
    text-align: center;
    color: var(--bronze-text);
  }
  .brand-name {
    font-family: var(--serif);
    font-weight: 400;
    line-height: 1;
  }
  .brand-place {
    font-family: var(--sans);
    font-size: 8px;
    letter-spacing: 2px;
    text-align: right;
  }
  .card-front .brand { left: 315px; top: 110px; width: 240px; }
  .card-front .brand-name { font-size: 56px; }
  .card-front .brand-place { margin-top: 14px; padding-right: 10px; }

  .marble {
    position: absolute;
    inset: 0;
    background:
      radial-gradient(ellipse at 30% 20%, rgba(150,150,150,0.35), transparent 55%),
      radial-gradient(ellipse at 85% 85%, rgba(120,120,120,0.35), transparent 50%),
      linear-gradient(160deg, var(--marble-light), var(--marble-mid) 60%, var(--marble-light));
  }
  .card-back .brand { left: 150px; top: 92px; width: 300px; }
  .card-back .brand-name { font-size: 72px; }
  .card-back .brand-place { margin-top: 22px; padding-right: 62px; }

  .social-list {
    position: absolute;
    right: 14px;
    top: 34px;
    list-style: none;
    display: flex;
    gap: 8px;
    font-family: var(--serif);
    font-size: 9px;
    color: var(--bronze-text);
  }
  .social-list li { display: flex; align-items: center; gap: 3px; }
  .social-dot { width: 8px; height: 8px; border-radius: 50%; background: var(--bronze); }

  .web-address {
    position: absolute;
    left: 0;
    right: 0;
    top: 287px;
    text-align: center;
    font-family: var(--serif);
    font-weight: 700;
    font-size: 15px;
    letter-spacing: 3.6px;
    color: var(--bronze-text);
  }
</style>
</head>
<body>

<section class="card card-front" aria-label="Card front">
  <svg class="front-shape" viewBox="0 0 600 343" aria-hidden="true">
    <path d="M0 0 H315 C240 60 220 190 300 280 C330 310 365 330 400 343 H0 Z" fill="var(--bronze)"/>
    <path d="M308 4 C228 68 212 200 300 290 C325 315 360 333 390 343" fill="none" stroke="#ffffff" stroke-width="1.5"/>
  </svg>

  <div class="contact-block">
    <p class="person-name">JORDAN VALE</p>
    <p class="person-role">CEO/FOUNDER</p>
    <p class="address">4720 N.Alder Crest Ave<br>Beverly Hills<br>CA 90210</p>
    <ul class="contact-list">
      <li><svg viewBox="0 0 24 24"><path d="M6.6 10.8a15.1 15.1 0 0 0 6.6 6.6l2.2-2.2c.3-.3.7-.4 1-.2 1.1.4 2.3.6 3.6.6.6 0 1 .4 1 1V20c0 .6-.4 1-1 1A17 17 0 0 1 3 4c0-.6.4-1 1-1h3.5c.6 0 1 .4 1 1 0 1.3.2 2.5.6 3.6.1.3 0 .7-.2 1z"/></svg>555 014 2290</li>
      <li><svg viewBox="0 0 24 24"><path d="M2 5h20v14H2z M4 7v.5l8 5 8-5V7l-8 5z" fill-rule="evenodd"/></svg>news@lashverastudiolounge</li>
      <li><svg viewBox="0 0 24 24"><circle cx="12" cy="12" r="10"/><path d="M2 12h20M12 2c3 3 3 17 0 20M12 2c-3 3-3 17 0 20" stroke="#8a674d" stroke-width="1.5" fill="none"/></svg>www.lashverastudio.example</li>
    </ul>
  </div>

  <div class="brand">
    <p class="brand-name">Lashvera</p>
    <p class="brand-place">BEVERLY HILLS</p>
  </div>
</section>

<section class="card card-back" aria-label="Card back">
  <div class="marble" role="img" aria-label="Grey and white marble texture background"></div>

  <ul class="social-list">
    <li><span class="social-dot"></span>Circlebook</li>
    <li><span class="social-dot"></span>Snapgrid</li>
  </ul>

  <div class="brand">
    <p class="brand-name">Lashvera</p>
    <p class="brand-place">BEVERLY HILLS</p>
  </div>

  <p class="web-address">www.lashverastudio.example</p>
</section>

</body>
</html>
```